Premium Gold Vodka Label Design

English ------------------- We need a label for a Vodka Bottle. Its a sparkling premium vodka with gold inside. The design should look premium. We tried it on our selves but it looks horrible. Therefore we need your help. The current name is lumora K, but we are open for any better suggestion. We attached the selfmade design. The label will be printed on the bottle. We have other design jobs for you (logo, other sorts)! English ------------------------ We need a label for a vodka bottle. This is a premium vodka which is offset with gold. The design should look like this. We have tried so far and failed. That is why we need your support. The name is so far lumora K. If you have better suggestions we would be pleased about other suggestions / ideas. In the appendix the failed design is stored. The label is to be applied by screen printing. In the case of good work follow-up projects are guaranteed (logo, other varieties, etc)!
Updates

Project Deadline Extended
Reason: We need more time for the decision.

Target Market(s)

USA

Colors

Designer to choose colors to be used in the design.

Requirements
Must have
• English ------------------------ The needed text is on our selfmade label that is attached. English ------------------------ The required texts are stored in the attached design.
Nice to have
• English ------------------------ Transparent places are allowed because we want to print the label on the bottom. English ------------------------ As the label is applied by screen printing, transparent areas are also possible.

```html
<!DOCTYPE html>
<html lang="en">
<head>
<meta charset="utf-8">
<title>Lumora K – 24 KT Premium Gold Sparkling Vodka Label</title>
<link rel="stylesheet" href="https://fonts.googleapis.com/css2?family=Barlow:wght@400;500&family=Barlow+Condensed:wght@300;400&family=Playfair+Display:wght@700&display=swap">
<style>
  :root {
    --gold: #e2b93b;
    --gold-light: #f6dc78;
    --gold-deep: #a8781c;
    --label-black: #000000;
    --band-dark: #5a0000;
    --band-bright: #d10000;
    --page: #ffffff;
  }
  * { margin: 0; padding: 0; box-sizing: border-box; }
  html, body {
    width: 696px;
    height: 1200px;
    overflow: hidden;
    background: var(--page);
  }
  .label {
    position: relative;
    width: 696px;
    height: 1200px;
  }
  .label-frame {
    position: absolute;
    inset: 0;
  }
  .brand-mark {
    position: absolute;
    top: 240px;
    left: 0;
    width: 100%;
    text-align: center;
    font-family: "Playfair Display", Georgia, serif;
    font-weight: 700;
    font-size: 66px;
    color: var(--gold);
    letter-spacing: 1px;
  }
  .karat {
    position: absolute;
    top: 462px;
    left: 0;
    width: 100%;
    text-align: center;
    font-family: "Barlow", Arial, sans-serif;
    font-weight: 400;
    font-size: 76px;
    color: var(--gold);
    letter-spacing: 2px;
  }
  .tagline {
    position: absolute;
    top: 642px;
    left: 0;
    width: 100%;
    text-align: center;
    font-family: "Barlow", Arial, sans-serif;
    font-weight: 400;
    font-size: 35px;
    color: var(--gold);
    word-spacing: 4px;
  }
  .product-band {
    position: absolute;
    top: 781px;
    left: 15px;
    width: 666px;
    height: 118px;
    background: linear-gradient(90deg, var(--band-dark) 0%, #9a0000 45%, var(--band-bright) 100%);
    border-top: 3px solid var(--gold);
    border-bottom: 3px solid var(--gold);
    display: flex;
    align-items: center;
    justify-content: center;
  }
  .product-name {
    font-family: "Barlow Condensed", Arial Narrow, sans-serif;
    font-weight: 300;
    font-size: 84px;
    color: var(--gold-light);
    letter-spacing: 2px;
    line-height: 1;
  }
  .origin {
    position: absolute;
    top: 936px;
    left: 0;
    width: 100%;
    text-align: center;
    font-family: "Barlow", Arial, sans-serif;
    font-weight: 400;
    font-size: 32px;
    line-height: 48px;
    color: var(--gold);
  }
  .specs {
    position: absolute;
    top: 1098px;
    left: 0;
    width: 100%;
    display: flex;
    justify-content: center;
    align-items: center;
    font-family: "Barlow", Arial, sans-serif;
    font-weight: 500;
    font-size: 19px;
    color: var(--gold);
  }
  .specs .divider {
    width: 2px;
    height: 26px;
    background: var(--gold);
    margin: 0 18px;
  }
</style>
</head>
<body>
<main class="label">
  <svg class="label-frame" width="696" height="1200" viewBox="0 0 696 1200" aria-hidden="true">
    <defs>
      <linearGradient id="goldEdge" x1="0" y1="0" x2="1" y2="1">
        <stop offset="0" stop-color="#f6dc78"/>
        <stop offset="0.35" stop-color="#c9962a"/>
        <stop offset="0.6" stop-color="#f3d36a"/>
        <stop offset="1" stop-color="#a8781c"/>
      </linearGradient>
    </defs>
    <path class="label-body"
      d="M70 6 H626 A64 64 0 0 0 690 70 V1130 A64 64 0 0 0 626 1194 H70 A64 64 0 0 0 6 1130 V70 A64 64 0 0 0 70 6 Z"
      fill="var(--label-black)" stroke="url(#goldEdge)" stroke-width="8"/>
    <path class="label-inner-rule"
      d="M76 17 H620 A58 58 0 0 0 679 76 V1124 A58 58 0 0 0 620 1183 H76 A58 58 0 0 0 17 1124 V76 A58 58 0 0 0 76 17 Z"
      fill="none" stroke="url(#goldEdge)" stroke-width="2"/>
  </svg>

  <div class="brand-mark">Lumora K</div>
  <div class="karat">24 KT</div>
  <div class="tagline">PREMIUM GOLD SPARKLING</div>

  <div class="product-band">
    <span class="product-name">VODKA</span>
  </div>

  <div class="origin">
    DISTILLED 8 FILTERED<br>
    MADE IN GERMANY
  </div>

  <div class="specs">
    <span>40% ALC VOL</span>
    <span class="divider"></span>
    <span>200 ML</span>
    <span class="divider"></span>
    <span>80 PROOF</span>
  </div>
</main>
</body>
</html>
```